Dynamic Business Card for Sports Supplements Company

Hi! I'm looking for an awesome business card to match my existing sports supplement company. I have uploaded my current company logo and screenshot of the front page of my website.

I would like to have something dynamic and interesting and utilize the colors in the website - the reds and purples

The business card should be double sided and focus on a unique eye-catching design on the back and include all the relevant company info.

Most importantly, it should say somewhere: "Sign up on our website for a coupon code."

Target Market(s)

Mostly for women gym goers but it shouldn't be too feminine. It should be in keeping with the website design. It should flow and clearly be connected to it

Industry/Entity Type

Business

Contact Information for Business Card

Lorraine K. Vestal
CEO
LVestal@Quorvanexco.com
www.quorvanexco.com
555.417.3820
P.O. Box 47315
Fernvale, Oregon 00000

Sign up on our website for a coupon code

Font styles to use
Serif
Sans Serif
Other font styles liked:
• Novecento font family and "Quorvanex" is in AR Destine font

Requirements
Must have
• One side should be a bold Quorvanex logo design. Even just the symbol itself may be o.k. (see attached file)

```html
<!DOCTYPE html>
<html lang="en">
<head>
<meta charset="utf-8">
<title>Quorvanex Business Card</title>
<link rel="stylesheet" href="https://fonts.googleapis.com/css2?family=Saira:wght@400;500;700&display=swap">
<style>
  :root {
    --backdrop: #b5b5b5;
    --card-white: #ffffff;
    --ink: #1c1c1c;
    --accent-red: #e0262b;
    --back-dark: #2b2b2b;
    --back-darker: #1a1a1a;
    --on-dark: #ffffff;
  }
  * { margin: 0; padding: 0; box-sizing: border-box; }
  html, body { width: 1200px; height: 900px; overflow: hidden; }
  body {
    background: var(--backdrop);
    font-family: "Saira", Arial, sans-serif;
    color: var(--ink);
    position: relative;
  }
  .card {
    position: absolute;
    top: 184px;
    height: 490px;
    border-radius: 14px;
    overflow: hidden;
  }
  .card-front { left: 299px; width: 301px; background: var(--card-white); }
  .card-back { left: 645px; width: 305px; }

  .brand {
    position: absolute;
    left: 0; right: 0;
    text-align: center;
  }
  .brand-name {
    display: inline-flex;
    align-items: center;
    gap: 8px;
    font-weight: 700;
    letter-spacing: 1.5px;
    line-height: 1;
  }
  .brand-mark {
    display: inline-block;
    width: 14px; height: 14px;
    background: var(--accent-red);
  }
  .brand-tagline {
    display: block;
    font-weight: 500;
    text-transform: uppercase;
    line-height: 1;
  }

  .card-front .brand { top: 166px; }
  .card-front .brand-name { font-size: 31px; color: var(--ink); }
  .card-front .brand-tagline { font-size: 10.5px; letter-spacing: 2.6px; margin-top: 6px; color: var(--ink); }

  .person { position: absolute; left: 33px; top: 275px; }
  .person-name {
    font-size: 17.5px;
    font-weight: 400;
    color: var(--accent-red);
    letter-spacing: 2.2px;
    text-transform: uppercase;
    line-height: 1.2;
  }
  .person-title { font-size: 15px; font-weight: 500; line-height: 1.3; }

  .contact-list {
    position: absolute;
    left: 33px; top: 329px;
    list-style: none;
    font-size: 14px;
    line-height: 22.5px;
  }
  .contact-list li { display: flex; align-items: center; gap: 7px; }
  .contact-icon { width: 13px; height: 13px; fill: var(--accent-red); flex: none; }

  .address {
    position: absolute;
    left: 33px; top: 409px;
    font-style: normal;
    font-size: 14px;
    line-height: 18px;
  }

  .back-texture {
    position: absolute; inset: 0;
    background: linear-gradient(180deg, var(--back-dark) 0%, #262626 55%, var(--back-darker) 100%);
  }
  .card-back .brand { top: 280px; color: var(--on-dark); }
  .card-back .brand-name { font-size: 34px; color: var(--on-dark); }
  .card-back .brand-tagline { font-size: 11px; letter-spacing: 2.8px; margin-top: 7px; color: var(--on-dark); }
  .coupon-note {
    position: absolute;
    left: 0; right: 0; top: 406px;
    text-align: center;
    color: var(--on-dark);
    font-size: 14px;
    line-height: 18px;
  }
</style>
</head>
<body>
  <section class="card card-front">
    <div class="brand">
      <span class="brand-name"><span class="brand-mark"></span>QUORVANEX</span>
      <span class="brand-tagline">Your Strength Companion</span>
    </div>

    <div class="person">
      <p class="person-name">Lorraine K. Vestal</p>
      <p class="person-title">CEO</p>
    </div>

    <ul class="contact-list">
      <li>
        <svg class="contact-icon" viewBox="0 0 16 16" aria-hidden="true"><path d="M1 5c0-2 3-3 7-3s7 1 7 3v1.5h-3.5V5h-7v1.5H1zM3 8l2-2h6l2 2v6H3zM8 9a2 2 0 1 0 0 4a2 2 0 1 0 0-4z"/></svg>
        555.417.3820
      </li>
      <li>
        <svg class="contact-icon" viewBox="0 0 16 16" aria-hidden="true"><path d="M1 3h14v10H1zM2.2 4.2V5l5.8 4 5.8-4v-.8L8 8.2z" fill-rule="evenodd"/></svg>
        LVestal@Quorvanexco.com
      </li>
      <li>
        <svg class="contact-icon" viewBox="0 0 16 16" aria-hidden="true"><circle cx="8" cy="8" r="7"/><path d="M4 5l3 1 1 3-2 2-1 3M10 3l1 2 3 1M11 10l2 1" stroke="#fff" stroke-width="1.2" fill="none"/></svg>
        www.quorvanexco.com
      </li>
    </ul>

    <address class="address">
      P.O. Box 47315<br>
      Fernvale, Oregon 00000
    </address>
  </section>

  <section class="card card-back">
    <div class="back-texture" role="img" aria-label="Dark charcoal wood grain texture"></div>
    <div class="brand">
      <span class="brand-name"><span class="brand-mark"></span>QUORVANEX</span>
      <span class="brand-tagline">Your Strength Companion</span>
    </div>
    <p class="coupon-note">Sign up<br>on our website for a coupon code</p>
  </section>
</body>
</html>
```